Moravel Aesthetic Doctor

I require an elegant, luxurious looking business card for my aesthetic business. I am a doctor and that will set me aside from competitors. I am planning to provide home and spa based treatments to clients with high expectations. I have attached my logo.

```html
<!DOCTYPE html>
<html lang="en">
<head>
<meta charset="utf-8">
<title>Moravel Aesthetic Doctor – Business Card</title>
<link rel="stylesheet" href="https://fonts.googleapis.com/css2?family=Montserrat:wght@400;500&display=swap">
<style>
  :root {
    --backdrop: #e4e0da;
    --card: #ffffff;
    --ink: #3c3c3e;
    --wordmark: #8c8f94;
    --accent: #3b8fd8;
    --accent-soft: #a9d3f0;
  }
  * { box-sizing: border-box; margin: 0; padding: 0; }
  html, body { width: 1200px; height: 896px; overflow: hidden; }
  body {
    background: var(--backdrop);
    font-family: "Montserrat", sans-serif;
    color: var(--ink);
    position: relative;
  }
  .card {
    position: absolute;
    left: 302px;
    width: 620px;
    height: 353px;
    background: var(--card);
    box-shadow: 0 2px 8px rgba(0,0,0,0.18);
  }
  .card--front { top: 95px; }
  .card--back { top: 469px; }

  .brand { position: absolute; display: flex; align-items: center; }
  .brand__dot { border-radius: 50%; background: var(--accent-soft); flex: none; }
  .brand__name {
    color: var(--wordmark);
    font-weight: 400;
    line-height: 1;
    letter-spacing: 0.04em;
  }
  .brand__name span { display: block; }

  .card--front .brand { left: 128px; top: 76px; gap: 20px; }
  .card--front .brand__dot { width: 94px; height: 94px; }
  .card--front .brand__line1 { font-size: 48px; }
  .card--front .brand__line2 { font-size: 20.5px; margin-top: 8px; letter-spacing: 0.06em; }

  .services {
    position: absolute;
    top: 250px;
    left: 0;
    width: 100%;
    text-align: center;
    font-size: 13.5px;
    line-height: 18px;
  }
  .tagline {
    position: absolute;
    top: 286px;
    left: 0;
    width: 100%;
    text-align: center;
    font-size: 19px;
    color: var(--accent);
  }

  .card--back .brand { left: 56px; top: 143px; gap: 12px; }
  .card--back .brand__dot { width: 64px; height: 64px; }
  .card--back .brand__line1 { font-size: 30px; }
  .card--back .brand__line2 { font-size: 12.8px; margin-top: 6px; letter-spacing: 0.05em; }

  .divider {
    position: absolute;
    left: 319px;
    top: 113px;
    width: 1.5px;
    height: 126px;
    background: var(--accent);
  }
  .details { position: absolute; left: 337px; top: 110px; }
  .doctor { font-size: 19.5px; font-weight: 400; line-height: 24px; }
  .doctor small { font-size: 9.5px; color: var(--accent); margin-left: 4px; letter-spacing: 0.03em; }
  .qualification { font-size: 14px; line-height: 18px; color: var(--accent); margin-top: 4px; }
  .contacts { list-style: none; margin-top: 12px; font-size: 14px; }
  .contacts li { display: flex; align-items: center; height: 19px; }
  .contacts svg { width: 11px; height: 11px; margin-right: 8px; fill: var(--accent); }
  .social { display: inline-flex; gap: 8px; margin-left: 22px; }
  .social i { width: 11px; height: 11px; border-radius: 50%; background: var(--accent); display: block; }
</style>
</head>
<body>
  <section class="card card--front">
    <div class="brand">
      <div class="brand__dot"></div>
      <p class="brand__name"><span class="brand__line1">MORAVEL</span><span class="brand__line2">AESTHETIC DOCTOR</span></p>
    </div>
    <p class="services">Dermal injectables - Plasma facials - Microneedling<br>Skin boosters - Excessive sweating</p>
    <p class="tagline">Home and Spa Based Treatments</p>
  </section>

  <section class="card card--back">
    <div class="brand">
      <div class="brand__dot"></div>
      <p class="brand__name"><span class="brand__line1">MORAVEL</span><span class="brand__line2">AESTHETIC DOCTOR</span></p>
    </div>
    <div class="divider"></div>
    <div class="details">
      <p class="doctor">Dr Elsa Brandt<small>MRCPCH MD</small></p>
      <p class="qualification">Australasian Diploma<br>&nbsp;of Aesthetic Medicine</p>
      <ul class="contacts">
        <li><svg viewBox="0 0 24 24"><path d="M6.6 10.8a15 15 0 0 0 6.6 6.6l2.2-2.2a1 1 0 0 1 1-.25 11.4 11.4 0 0 0 3.6.57 1 1 0 0 1 1 1V20a1 1 0 0 1-1 1A17 17 0 0 1 3 4a1 1 0 0 1 1-1h3.5a1 1 0 0 1 1 1c0 1.25.2 2.45.57 3.6a1 1 0 0 1-.25 1z"/></svg>0800 555 019</li>
        <li><svg viewBox="0 0 24 24"><path d="M2 5h20v14H2z M2 5l10 8 10-8" fill="none" stroke="#3b8fd8" stroke-width="0"/><path d="M2 6.5V19h20V6.5l-10 7.5z M3 5l9 6.8L21 5z"/></svg>elsa@moravel.co.nz</li>
        <li><svg viewBox="0 0 24 24"><circle cx="12" cy="12" r="9.5" fill="none" stroke="#3b8fd8" stroke-width="2"/><path d="M2.5 12h19M12 2.5c-3 3-3 16 0 19M12 2.5c3 3 3 16 0 19" fill="none" stroke="#3b8fd8" stroke-width="1.6"/></svg>www.moravel.co.nz<span class="social"><i></i><i></i></span></li>
      </ul>
    </div>
  </section>
</body>
</html>
```